Norrell Advisory WA Business Card

Create an interesting, eye catching and colourful two sided business card. We are a business consulting operation assisting SME's improve all areas of their business. We provide consulting services to assist SME's to create a culture of continuous improvement, making a positive difference in the business. Our tag line is Small changes, big rewards. We want to create a well recognised, innovative brand that can be continued throughout our website, social media and email correspondence.

Target Market(s)

Small to Medium Enterprise Business Owners

Industry/Entity Type

Business Consultant

Contact Information for Business Card

Name of Business: Norrell Advisory - Steady Steps Lasting Gains
Derek Holloway Ph 0407385510 Megan Holloway Ph 0407913847
Email norrelladvisorywa@mailbox-example.com
Web address TBA
FaceBook page TBA

BACKSIDE OF CARD

Providing assistance with:

• Organisation & Efficiency
• Revenue generation & Marketing
• Financial Management
• Production quality & delivery
• Systems & Process documentation
• Exit Strategy

Font styles to use
Other font styles liked:
• Calibri

Colors

Designer to choose colors to be used in the design.

Requirements
Must have
• Calibri font

```html
<!DOCTYPE html>
<html lang="en">
<head>
<meta charset="utf-8">
<title>Norrell Advisory WA Business Card</title>
<link rel="stylesheet" href="https://fonts.googleapis.com/css2?family=Carlito:wght@400;700&display=swap">
<style>
  :root {
    --page: #e6e6e6;
    --card-dark: #2f2e2e;
    --card-light: #ffffff;
    --brand-blue: #0e7cc1;
    --ink-dark: #2c2c2c;
    --ink-grey: #555555;
    --tag-grey: #666666;
    --white: #ffffff;
    --mark-yellow: #f6c630;
    --mark-blue: #2a9ad6;
    --mark-red: #e8443a;
    --mark-green: #7bbb3a;
  }
  * { margin: 0; padding: 0; box-sizing: border-box; }
  html, body {
    width: 1125px; height: 1200px; overflow: hidden;
    background: var(--page);
    font-family: "Carlito", Calibri, sans-serif;
  }
  .canvas { position: relative; width: 1125px; height: 1200px; }
  .card {
    position: absolute; left: 157px; width: 826px; height: 472px;
    box-shadow: 0 2px 4px rgba(0,0,0,0.25);
  }
  .card--front { top: 106px; background: var(--card-dark); }
  .card--back { top: 640px; background: var(--card-light); }

  /* front */
  .contact-people { position: absolute; left: 48px; top: 222px; }
  .person-name { color: var(--brand-blue); font-weight: 700; font-size: 29px; line-height: 1; }
  .person-phone { color: var(--white); font-weight: 700; font-size: 19px; line-height: 1; margin-top: 5px; margin-bottom: 18px; }
  .contact-lines { position: absolute; left: 48px; top: 362px; list-style: none; }
  .contact-lines li {
    display: flex; align-items: center; gap: 12px;
    color: var(--white); font-size: 19px; line-height: 25px;
  }
  .contact-icon { width: 17px; height: 17px; flex: none; }
  .feature-area {
    position: absolute; left: 357px; top: 16px; width: 452px; height: 444px;
    background: linear-gradient(135deg, var(--mark-blue) 15%, var(--mark-yellow) 40%, var(--mark-red) 62%, var(--mark-green) 85%);
    clip-path: polygon(50% 0, 100% 50%, 50% 100%, 0 50%);
  }

  /* back */
  .brand-block { position: absolute; left: 67px; top: 169px; width: 300px; text-align: center; }
  .brand-square { width: 70px; height: 70px; margin: 0 auto 36px; background: var(--brand-blue); }
  .brand-name { color: var(--ink-dark); font-weight: 700; font-size: 28px; line-height: 1; letter-spacing: 0.5px; }
  .brand-tagline { color: var(--tag-grey); font-size: 16px; letter-spacing: 2px; margin-top: 4px; }
  .services { position: absolute; left: 400px; top: 128px; }
  .services-heading { color: var(--brand-blue); font-weight: 700; font-size: 30px; line-height: 1; margin-bottom: 14px; }
  .services-list { list-style: none; }
  .services-list li {
    display: flex; align-items: center; gap: 9px;
    color: var(--ink-grey); font-size: 21px; line-height: 26.2px;
  }
  .services-list li::before {
    content: ""; width: 12px; height: 12px; background: var(--mark-blue); flex: none;
  }
</style>
</head>
<body>
<div class="canvas">
  <section class="card card--front">
    <div class="contact-people">
      <p class="person-name">Derek Holloway</p>
      <p class="person-phone">0407385510</p>
      <p class="person-name">Megan Holloway</p>
      <p class="person-phone">0407913847</p>
    </div>
    <ul class="contact-lines">
      <li>
        <svg class="contact-icon" viewBox="0 0 16 16"><rect x="1" y="3" width="14" height="10" fill="#0e7cc1"/><path d="M1 3 L8 9 L15 3" fill="none" stroke="#2f2e2e" stroke-width="1.5"/></svg>
        norrelladvisorywa@mailbox-example.com
      </li>
      <li>
        <svg class="contact-icon" viewBox="0 0 16 16"><circle cx="8" cy="8" r="7" fill="#0e7cc1"/><ellipse cx="8" cy="8" rx="3" ry="7" fill="none" stroke="#2f2e2e" stroke-width="1"/><line x1="1" y1="8" x2="15" y2="8" stroke="#2f2e2e" stroke-width="1"/></svg>
        www.norrelladvisorywa.com
      </li>
      <li>
        <svg class="contact-icon" viewBox="0 0 16 16"><rect x="1" y="1" width="14" height="14" fill="#0e7cc1"/></svg>
        norrelladvisorywa
      </li>
    </ul>
    <div class="feature-area" role="img" aria-label="Large colourful brand mark decoration in blue, yellow, red and green"></div>
  </section>

  <section class="card card--back">
    <div class="brand-block">
      <div class="brand-square"></div>
      <p class="brand-name">NORRELL ADVISORY</p>
      <p class="brand-tagline">STEADY STEPS LASTING GAINS</p>
    </div>
    <div class="services">
      <h2 class="services-heading">Providing assistance with</h2>
      <ul class="services-list">
        <li>Organisation &amp; Efficiency</li>
        <li>Revenue generation &amp; Marketing</li>
        <li>Financial Management</li>
        <li>Production quality &amp; delivery</li>
        <li>Systems &amp; Process documentation</li>
        <li>Exit Strategy</li>
      </ul>
    </div>
  </section>
</div>
</body>
</html>
```